Modern Business Card

Modern professional business card with more than just logo and demographic info. Something memorable.

We are a trendy/modern chiropractic group with an emphasis on neurology, hence the minimalist-type brain logo. We want to convey that modern and technical aspect with professionalism and the elite nature of our practice environment.

```html
<!DOCTYPE html>
<html lang="en">
<head>
<meta charset="utf-8">
<title>Meridian Spine – Business Card</title>
<link rel="stylesheet" href="https://fonts.googleapis.com/css2?family=Quattrocento:wght@400&family=Saira+Semi+Condensed:wght@500&display=swap">
<style>
  :root {
    --page-bg: #b9b9b9;
    --brand-blue: #3d62a0;
    --brand-blue-deep: #375b97;
    --ink: #1c1a1a;
    --ink-soft: #3a3535;
    --band-dark: #3b3133;
    --cream: #ece9e4;
    --card-light: #f5f5f5;
    --card-shade: #e2e3e5;
  }
  * { box-sizing: border-box; margin: 0; padding: 0; }
  html, body {
    width: 1200px; height: 576px; overflow: hidden;
    background: var(--page-bg);
  }
  .canvas { position: relative; width: 1200px; height: 576px; }

  .card {
    position: absolute; top: 138px; height: 293px;
    border-radius: 10px; overflow: hidden;
    font-family: "Quattrocento", Georgia, serif;
  }

  /* Back side */
  .card-back {
    left: 82px; width: 484px;
    background: linear-gradient(180deg, var(--brand-blue) 0%, var(--brand-blue-deep) 100%);
    color: var(--cream);
    text-align: center;
  }
  .back-wordmark {
    position: absolute; left: 0; right: 0; top: 98px;
    line-height: 1;
  }
  .back-wordmark .word-main { display: block; font-size: 66px; letter-spacing: 1px; }
  .back-wordmark .word-sub { display: block; font-size: 38px; letter-spacing: 1px; margin-top: 0px; }

  /* Front side */
  .card-front {
    left: 602px; width: 480px;
    background: linear-gradient(135deg, var(--card-light) 0%, var(--card-shade) 100%);
    color: var(--ink-soft);
  }
  .front-brand {
    position: absolute; left: 27px; top: 48px;
    display: flex; align-items: center; gap: 12px;
    color: var(--ink);
  }
  .brand-square { width: 38px; height: 38px; background: var(--brand-blue); }
  .brand-name { line-height: 0.95; }
  .brand-name .word-main { display: block; font-size: 48px; letter-spacing: 0.5px; }
  .brand-name .word-sub { display: block; font-size: 28px; letter-spacing: 0.5px; }

  .person { position: absolute; left: 27px; top: 162px; }
  .person-name {
    font-family: "Saira Semi Condensed", "Arial Narrow", sans-serif;
    font-weight: 500; font-size: 19px; color: var(--brand-blue);
  }
  .person-title { font-size: 13px; margin-top: 2px; }

  .address { position: absolute; left: 27px; top: 228px; font-size: 13px; line-height: 18px; }

  .contact-list {
    position: absolute; left: 257px; top: 162px;
    list-style: none; font-size: 12.5px; line-height: 18.5px;
  }
  .contact-list li { display: flex; align-items: center; gap: 9px; }
  .contact-list svg { width: 11px; height: 11px; fill: var(--brand-blue); flex: none; }

  .footer-band-dark {
    position: absolute; left: 0; right: 0; bottom: 0; height: 12px;
    background: var(--band-dark);
  }
  .footer-band-blue {
    position: absolute; left: 194px; right: 0; bottom: 0; height: 35px;
    background: var(--brand-blue);
    clip-path: polygon(20px 0, 100% 0, 100% 100%, 0 100%);
    color: var(--cream); font-size: 12.5px;
    display: flex; align-items: center; justify-content: center;
    padding-left: 20px;
  }
</style>
</head>
<body>
<main class="canvas">
  <section class="card card-back" aria-label="Card back">
    <div class="back-wordmark">
      <span class="word-main">MERIDIAN</span>
      <span class="word-sub">SPINE</span>
    </div>
  </section>

  <section class="card card-front" aria-label="Card front">
    <div class="front-brand">
      <div class="brand-square"></div>
      <div class="brand-name">
        <span class="word-main">MERIDIAN</span>
        <span class="word-sub">SPINE</span>
      </div>
    </div>

    <div class="person">
      <div class="person-name">Daniel Reyes Hart</div>
      <div class="person-title">Managing Director</div>
    </div>

    <address class="address" style="font-style:normal">
      418 Harbor Lane, Westfield,<br>
      Lakeview, US 204817
    </address>

    <ul class="contact-list">
      <li>
        <svg viewBox="0 0 12 12" aria-hidden="true"><path d="M1 4c0-2 2-3 5-3s5 1 5 3v1H8.5V3.8h-5V5H1z M3 6h6l2 4v1H1v-1z M6 7a1.4 1.4 0 1 0 0 2.8A1.4 1.4 0 0 0 6 7z"/></svg>
        555-014-2020
      </li>
      <li>
        <svg viewBox="0 0 12 12" aria-hidden="true"><path d="M0 2h12v8H0z" /><path d="M0.8 2.6 6 6.6l5.2-4" fill="none" stroke="#f0f0f0" stroke-width="1"/></svg>
        daniel@meridianspine.com
      </li>
      <li>
        <svg viewBox="0 0 12 12" aria-hidden="true"><circle cx="6" cy="6" r="5.5"/><path d="M0.5 6h11M6 0.5v11M6 0.5c-3 3-3 8 0 11M6 0.5c3 3 3 8 0 11" fill="none" stroke="#f0f0f0" stroke-width="0.7"/></svg>
        www.meridianspine.com
      </li>
    </ul>

    <div class="footer-band-dark"></div>
    <div class="footer-band-blue">Meridian Spine LLC</div>
  </section>
</main>
</body>
</html>
```